Business card for medical clinic

I need an upmarket, modern medical/health business card for my clinic

Contact Information for Business Card

name, address, email, qr code

```html
<!DOCTYPE html>
<html lang="en">
<head>
<meta charset="utf-8">
<title>Meridia Care Clinic – Business Card</title>
<link href="https://fonts.googleapis.com/css2?family=Cinzel:wght@600&family=Arimo:wght@400&display=swap" rel="stylesheet">
<style>
  :root {
    --backdrop: #9b9b9b;
    --paper: #fbfbfb;
    --brand-blue: #1b6fa8;
    --brand-light: #3aa6dc;
    --deep-blue: #145a87;
    --ink: #4a4a4a;
    --white: #ffffff;
  }
  * { margin: 0; padding: 0; box-sizing: border-box; }
  html, body {
    width: 1200px; height: 1020px; overflow: hidden;
    background: var(--backdrop);
  }
  .canvas {
    width: 1200px; height: 1020px;
    display: flex; flex-direction: column; align-items: center; justify-content: center;
    gap: 60px;
  }
  .card {
    width: 700px; height: 400px;
    position: relative;
    box-shadow: 0 14px 30px rgba(0,0,0,0.25);
  }
  .card--front { background: var(--paper); border-bottom: 4px solid var(--brand-light); }
  .card--back { background: var(--deep-blue); display: flex; align-items: center; justify-content: center; }

  .brand {
    display: flex; align-items: center; gap: 16px;
    font-family: "Cinzel", serif; font-weight: 600; letter-spacing: 2px;
  }
  .brand__mark { border-radius: 50%; border: 3px solid currentColor; flex: none; }
  .card--front .brand {
    position: absolute; top: 70px; left: 0; right: 0; justify-content: center;
    color: var(--brand-blue); font-size: 30px;
  }
  .card--front .brand__mark { width: 58px; height: 58px; }
  .card--back .brand { color: var(--white); font-size: 42px; }
  .card--back .brand__mark { width: 80px; height: 80px; }

  .person {
    position: absolute; top: 198px; right: 390px; text-align: right;
  }
  .person__name {
    font-family: "Cinzel", serif; font-weight: 600; font-size: 27px;
    color: var(--brand-blue); letter-spacing: 1px;
  }
  .person__role {
    font-family: "Arimo", sans-serif; font-size: 17px; color: var(--ink); margin-top: 2px;
  }
  .divider {
    position: absolute; top: 196px; left: 332px; width: 1px; height: 78px;
    background: var(--brand-light);
  }
  .contacts {
    position: absolute; top: 196px; left: 352px; list-style: none;
    font-family: "Arimo", sans-serif; font-size: 17px; color: var(--ink);
  }
  .contacts li { display: flex; align-items: center; gap: 9px; height: 27px; }
  .contacts svg { width: 14px; height: 14px; fill: var(--brand-light); flex: none; }
  .address {
    position: absolute; top: 305px; left: 0; right: 0; text-align: center;
    font-family: "Arimo", sans-serif; font-size: 17px; color: var(--ink);
  }
</style>
</head>
<body>
<main class="canvas">
  <section class="card card--front" aria-label="Card front">
    <div class="brand">
      <span class="brand__mark"></span>
      <span class="brand__name">Meridia Care Clinic</span>
    </div>
    <div class="person">
      <p class="person__name">DANIEL HART</p>
      <p class="person__role">Director/Founder</p>
    </div>
    <div class="divider"></div>
    <ul class="contacts">
      <li>
        <svg viewBox="0 0 16 16" aria-hidden="true"><path d="M3 1l3 3-2 2c1 2 3 4 5 5l2-2 3 3-2 3C6 14 2 10 1 3z"/></svg>
        05310 482 7716
      </li>
      <li>
        <svg viewBox="0 0 16 16" aria-hidden="true"><path d="M1 3h14v10H1z M2 4l6 5 6-5" fill="none" stroke="#3aa6dc" stroke-width="1.6"/></svg>
        info@meridiacareclinic.com
      </li>
      <li>
        <svg viewBox="0 0 16 16" aria-hidden="true"><circle cx="8" cy="8" r="7"/><path d="M1 8h14M8 1c-3 4-3 10 0 14M8 1c3 4 3 10 0 14" fill="none" stroke="#fbfbfb" stroke-width="1"/></svg>
        www.meridiacareclinic.com
      </li>
    </ul>
    <p class="address">7830 Harbor Lane Westfield AV 61027</p>
  </section>

  <section class="card card--back" aria-label="Card back">
    <div class="brand">
      <span class="brand__mark"></span>
      <span class="brand__name">Meridia Care Clinic</span>
    </div>
  </section>
</main>
</body>
</html>
```